Weightloss company needs Business Card

We want a business card that is clean and professional, yet portrays that we are a friendly, innovative, and versatile program designed to fit the needs of our clients.
I would like there to be 2 sides, one side having an appointment card, and the other side containing the logo and business information. There can be decorations on both sides. The logo is attached.

Target Market(s)

Men and women 40-60

Industry/Entity Type

Business

Contact Information for Business Card

Font styles to use
Sans Serif

Requirements
Must have
• The logo, space for business information
Nice to have
• The colors in the logo
Should not have
• No pictures of people or food

```html
<!DOCTYPE html>
<html lang="en">
<head>
<meta charset="utf-8">
<title>Turnabout Wellness – Business Card</title>
<link rel="stylesheet" href="https://fonts.googleapis.com/css2?family=Open+Sans:wght@400;600;700&display=swap">
<style>
  :root {
    --bg: #e9e6e1;
    --card: #ffffff;
    --card-shade: #ececec;
    --red: #e8173c;
    --red-soft: #f6c9d2;
    --red-faint: #fbe7eb;
    --cyan: #27b8d6;
    --ink: #555a5e;
    --ink-soft: #6d7276;
    --rule: #55595c;
  }
  * { box-sizing: border-box; margin: 0; padding: 0; }
  html, body { width: 1200px; height: 843px; overflow: hidden; }
  body {
    background: var(--bg);
    font-family: "Open Sans", Arial, sans-serif;
    display: flex; align-items: center; justify-content: center; gap: 40px;
  }
  .card {
    position: relative;
    width: 540px; height: 310px;
    border-radius: 18px;
    background: linear-gradient(160deg, var(--card) 55%, var(--card-shade));
    box-shadow: 0 6px 18px rgba(0,0,0,.18);
    overflow: hidden;
  }

  /* Appointment side */
  .appointment-title {
    position: absolute; left: 34px; top: 44px;
    color: var(--red); font-weight: 700; font-size: 20px;
  }
  .brand-name {
    color: var(--red); font-weight: 700; line-height: 1;
    display: flex; align-items: center; gap: 6px;
    white-space: nowrap;
  }
  .brand-dot { width: 9px; height: 9px; border-radius: 50%; background: var(--cyan); }
  .appointment .brand-name { position: absolute; right: 30px; top: 30px; font-size: 17px; }
  .slots { position: absolute; left: 34px; right: 30px; top: 96px; }
  .slot {
    display: flex; align-items: flex-end; gap: 10px;
    height: 42px; color: var(--ink); font-size: 14px;
  }
  .slot .line { border-bottom: 1.5px solid var(--rule); height: 1px; margin-bottom: 4px; }
  .slot .date-line { flex: 1.4; }
  .slot .time-line { flex: 1; }
  .slot .label-time { margin-left: 14px; }
  .notice {
    position: absolute; left: 34px; right: 30px; bottom: 26px;
    font-size: 11.5px; font-weight: 600; color: var(--ink);
  }

  /* Contact side */
  .front .brand-name { position: absolute; left: 30px; top: 30px; font-size: 24px; }
  .person { position: absolute; left: 30px; top: 70px; }
  .person-name { color: var(--red); font-size: 21px; font-weight: 600; letter-spacing: .5px; line-height: 1.1; }
  .person-role { color: var(--cyan); font-size: 14px; font-weight: 600; letter-spacing: .5px; }
  .address { margin-top: 6px; color: var(--ink-soft); font-size: 14px; line-height: 1.3; }
  .contacts { list-style: none; position: absolute; left: 30px; top: 178px; }
  .contacts li {
    display: flex; align-items: center; gap: 10px;
    color: var(--ink-soft); font-size: 14px; line-height: 21px;
  }
  .contacts svg { width: 13px; height: 13px; fill: var(--red); flex: none; }
  .turn-graphic {
    position: absolute; left: 300px; top: 62px;
    width: 210px; height: 230px;
    border-radius: 50%;
    background: radial-gradient(circle, var(--red-faint) 45%, var(--red-soft));
  }
</style>
</head>
<body>

  <section class="card appointment" aria-label="Appointment card">
    <h2 class="appointment-title">Next Appointment</h2>
    <div class="brand-name"><span>Turnabout Wellness</span><span class="brand-dot"></span></div>
    <div class="slots">
      <div class="slot"><span>Date</span><span class="line date-line"></span><span class="label-time">Time</span><span class="line time-line"></span><span>am/pm</span></div>
      <div class="slot"><span>Date</span><span class="line date-line"></span><span class="label-time">Time</span><span class="line time-line"></span><span>am/pm</span></div>
      <div class="slot"><span>Date</span><span class="line date-line"></span><span class="label-time">Time</span><span class="line time-line"></span><span>am/pm</span></div>
    </div>
    <p class="notice">Please give 24 hours notice of cancellation or a fee may be charged</p>
  </section>

  <section class="card front" aria-label="Contact card">
    <div class="turn-graphic" role="img" aria-label="Large red curved turnaround arrow decoration"></div>
    <div class="brand-name"><span>Turnabout Wellness</span><span class="brand-dot"></span></div>
    <div class="person">
      <h1 class="person-name">DANA REEVES</h1>
      <p class="person-role">CEO/FOUNDER</p>
      <p class="address">4120 Larkspur Road<br>Fairbanks, Alaska 99701</p>
    </div>
    <ul class="contacts">
      <li><svg viewBox="0 0 16 16"><path d="M3 1l3 3-2 2c1 2 3 4 5 5l2-2 3 3-2 3C6 15 1 10 1 3z"/></svg>907 555 0142</li>
      <li><svg viewBox="0 0 16 16"><path d="M4 0h8v16H4zM5.5 2v10h5V2z"/></svg>907 555 0187</li>
      <li><svg viewBox="0 0 16 16"><path d="M4 1h8v4H4zM1 6h14v7h-3v2H4v-2H1zM5 10v4h6v-4z"/></svg>907 555 0163</li>
      <li><svg viewBox="0 0 16 16"><path d="M1 3h14v10H1zM2 4l6 5 6-5v-0.5H2z"/></svg>hello@turnaboutwell.com</li>
      <li><svg viewBox="0 0 16 16"><circle cx="8" cy="8" r="7"/></svg>www.turnaboutwell.com</li>
    </ul>
  </section>

</body>
</html>
```